Business Card for Professional Photographer

I'm looking for an eye catching modern clean design that compliments my logo/ website fonts & colours.
I specialise in architecture, corporate & commercial photography so I'm marketing to professional clients rather than portrait / wedding clients.

I would prefer to not have a solid black design.

My logo brand guide is as follows :

Main front font. : Reislust
Main font colour : #fff
Slogan front font : Ubuntu Bold
Monogram front font : Venti Medium
Container colour : #fff

I need print ready files in pdf .png & .eps formats.

Included in the files below are some screen grabs as reference to font & colours etc.

```html
<!DOCTYPE html>
<html lang="en">
<head>
<meta charset="utf-8">
<title>North Light Studio – Business Card</title>
<link rel="stylesheet" href="https://fonts.googleapis.com/css2?family=Open+Sans:wght@300;400;700;800&family=Ubuntu:wght@700&display=swap">
<style>
  :root {
    --page-bg: #cfcfcf;
    --card: #2f2f31;
    --card-back: #2c2c2e;
    --emboss: #242426;
    --gold: #d9a93f;
    --gold-light: #f3d77a;
    --gold-dark: #b7862a;
    --white: #ffffff;
  }
  * { margin: 0; padding: 0; box-sizing: border-box; }
  html, body {
    width: 1200px; height: 1125px; overflow: hidden;
    background: var(--page-bg);
    font-family: "Open Sans", sans-serif;
  }
  .sheet {
    width: 1200px; height: 1125px;
    display: flex; flex-direction: column; align-items: center; justify-content: center;
    gap: 40px;
  }
  .card {
    position: relative;
    width: 900px; height: 514px;
    background: var(--card);
    overflow: hidden;
    box-shadow: 0 6px 18px rgba(0,0,0,0.25);
  }
  .card--back { background: var(--card-back); }
  .gold-edge {
    position: absolute; left: 0; right: 0; bottom: 0; height: 9px;
    background: linear-gradient(90deg, var(--gold-dark), var(--gold-light) 50%, var(--gold));
  }
  .brand {
    position: absolute; left: 0; right: 0;
    display: flex; align-items: center; justify-content: center; gap: 22px;
  }
  .brand__mark {
    width: 26px; height: 26px; border-radius: 50%;
    background: var(--gold);
  }
  .brand__text { display: flex; flex-direction: column; }
  .brand__name {
    font-weight: 300; font-size: 38px; letter-spacing: 7px;
    color: var(--white); line-height: 1.1;
  }
  .brand__tagline {
    font-family: "Ubuntu", sans-serif; font-weight: 700;
    font-size: 12px; letter-spacing: 5.4px; color: var(--gold);
    margin-top: 6px;
  }
  .card--front .brand { top: 110px; }
  .card--back .brand { top: 200px; }
  .card--back .brand__mark { background: var(--emboss); }
  .card--back .brand__name { color: var(--emboss); }
  .card--back .brand__tagline { color: var(--emboss); }

  .contact-block {
    position: absolute; top: 300px; left: 0; right: 0;
    display: flex; align-items: center;
  }
  .person {
    width: 395px; text-align: right; padding-right: 24px;
  }
  .person__name {
    font-weight: 800; font-size: 33px; color: var(--gold); letter-spacing: 0.5px;
  }
  .person__role {
    font-weight: 400; font-size: 23px; color: var(--white); margin-top: 2px;
  }
  .divider {
    width: 2px; height: 118px; background: var(--gold);
  }
  .details { list-style: none; padding-left: 26px; }
  .details li {
    display: flex; align-items: center; gap: 8px;
    font-size: 24px; color: var(--white); line-height: 1.3;
  }
  .details svg { width: 20px; height: 20px; flex: none; }
</style>
</head>
<body>
<main class="sheet">
  <section class="card card--back" aria-label="Card back">
    <div class="brand">
      <span class="brand__mark"></span>
      <div class="brand__text">
        <span class="brand__name">NORTH LIGHT STUDIO</span>
        <span class="brand__tagline">Architecture Corporate Commercial</span>
      </div>
    </div>
    <div class="gold-edge"></div>
  </section>

  <section class="card card--front" aria-label="Card front">
    <div class="brand">
      <span class="brand__mark"></span>
      <div class="brand__text">
        <span class="brand__name">NORTH LIGHT STUDIO</span>
        <span class="brand__tagline">Architecture Corporate Commercial</span>
      </div>
    </div>

    <div class="contact-block">
      <div class="person">
        <div class="person__name">DANIEL HARROW</div>
        <div class="person__role">Director</div>
      </div>
      <div class="divider"></div>
      <ul class="details">
        <li>
          <svg viewBox="0 0 24 24" aria-hidden="true"><path fill="var(--gold)" d="M6.6 10.8a15 15 0 0 0 6.6 6.6l2.2-2.2c.3-.3.7-.4 1-.2 1.1.4 2.3.6 3.6.6.6 0 1 .4 1 1V20c0 .6-.4 1-1 1A17 17 0 0 1 3 4c0-.6.4-1 1-1h3.5c.6 0 1 .4 1 1 0 1.3.2 2.5.6 3.6.1.3 0 .7-.2 1z"/></svg>
          555 014 2290
        </li>
        <li>
          <svg viewBox="0 0 24 24" aria-hidden="true"><path fill="var(--gold)" d="M2 5h20v14H2z"/><path fill="none" stroke="var(--card)" stroke-width="1.6" d="M2.5 5.5 12 13l9.5-7.5"/></svg>
          info@northlightstudio.com
        </li>
        <li>
          <svg viewBox="0 0 24 24" aria-hidden="true"><circle cx="12" cy="12" r="10" fill="var(--gold)"/><path fill="none" stroke="var(--card)" stroke-width="1.4" d="M2 12h20M12 2c3 3 3 17 0 20M12 2c-3 3-3 17 0 20"/></svg>
          www.northlightstudio.com
        </li>
      </ul>
    </div>
    <div class="gold-edge"></div>
  </section>
</main>
</body>
</html>
```